Tech business card design

We need an amazing business card design for our new business 'Pexla' a marketing tech startup based in Sydney, Australia. We provide an online marketplace for businesses to search and buy advertising media, connect with service providers and learn more about marketing. We wish to communicate 'cool tech', reliability and professionalism and design based around our logo.

Target Market(s)

Business Owners

Contact Information for Business Card

Name
Position
Email Address
Website
Phone Number

Font styles to use
Other font styles liked:
• Avenir & Avenir Next

Colors

Designer to choose colors to be used in the design.

```html
<!DOCTYPE html>
<html lang="en">
<head>
<meta charset="utf-8">
<title>Pexla Business Card</title>
<link rel="stylesheet" href="https://fonts.googleapis.com/css2?family=Nunito+Sans:wght@400;700;900&display=swap">
<style>
  :root {
    --stage: #e9eaee;
    --card: #ffffff;
    --navy: #1b2150;
    --grey: #7a7a7a;
    --rule: #b8b8b8;
    --ink: #222222;
  }
  * { margin: 0; padding: 0; box-sizing: border-box; }
  html, body { width: 1200px; height: 803px; overflow: hidden; }
  body {
    background: var(--stage);
    font-family: "Nunito Sans", Arial, sans-serif;
    position: relative;
  }
  .card {
    position: absolute;
    width: 560px;
    height: 320px;
    background: var(--card);
    box-shadow: 0 6px 18px rgba(0,0,0,0.18);
    overflow: hidden;
  }
  .card-front { left: 250px; top: 60px; }
  .card-back  { left: 390px; top: 420px; }
  .card-bands { position: absolute; inset: 0; width: 560px; height: 320px; }

  .wordmark {
    position: absolute;
    font-weight: 900;
    color: var(--navy);
    letter-spacing: -2px;
    line-height: 1;
  }
  .card-front .wordmark { left: 42px; top: 118px; font-size: 92px; }
  .card-back .wordmark { left: 0; right: 0; top: 92px; text-align: center; font-size: 118px; }

  .divider {
    position: absolute;
    left: 318px; top: 34px;
    width: 1px; height: 180px;
    background: var(--rule);
  }
  .contact {
    position: absolute;
    left: 332px; top: 34px;
    color: var(--ink);
    font-size: 13px;
    line-height: 1.35;
  }
  .contact .name { color: var(--navy); font-weight: 900; font-size: 17px; line-height: 1.1; }
  .contact .position { font-weight: 700; font-size: 12px; margin-bottom: 14px; }
  .contact .address { margin-bottom: 6px; }
  .contact .line { display: flex; align-items: center; gap: 5px; }
  .contact svg { width: 11px; height: 11px; flex: none; }
</style>
</head>
<body>
  <section class="card card-front" aria-label="Card front">
    <svg class="card-bands" viewBox="0 0 560 320" aria-hidden="true">
      <polygon points="0,302 328,302 352,262 360,262 334,320 0,320" fill="var(--grey)"/>
      <polygon points="360,252 560,252 560,268 352,268" fill="var(--navy)"/>
    </svg>
    <div class="wordmark">pexla</div>
    <div class="divider"></div>
    <div class="contact">
      <div class="name">SAM CARTER</div>
      <div class="position">Position</div>
      <div class="address">Street Name, City Name<br>Zipcode:012345</div>
      <div class="line">
        <svg viewBox="0 0 12 12"><path d="M2.5 1 L4.5 1 L5 3.5 L3.8 4.5 C4.5 6 6 7.5 7.5 8.2 L8.5 7 L11 7.5 L11 9.5 C11 10.5 10 11 9 11 C4.5 10.5 1.5 7.5 1 3 C1 2 1.5 1 2.5 1 Z" fill="var(--ink)"/></svg>
        <span>012-345-6789</span>
      </div>
      <div class="line">
        <svg viewBox="0 0 12 12"><rect x="0.5" y="2" width="11" height="8" fill="var(--ink)"/><path d="M0.8 2.3 L6 6.5 L11.2 2.3" stroke="#fff" stroke-width="1" fill="none"/></svg>
        <span>info@pexla.com</span>
      </div>
      <div class="line">
        <svg viewBox="0 0 12 12"><circle cx="6" cy="6" r="5" fill="none" stroke="var(--ink)" stroke-width="1"/><ellipse cx="6" cy="6" rx="2.2" ry="5" fill="none" stroke="var(--ink)" stroke-width="0.8"/><path d="M1 6 H11 M2 3.5 H10 M2 8.5 H10" stroke="var(--ink)" stroke-width="0.8"/></svg>
        <span>www.pexla.com</span>
      </div>
    </div>
  </section>

  <section class="card card-back" aria-label="Card back">
    <svg class="card-bands" viewBox="0 0 560 320" aria-hidden="true">
      <rect x="0" y="250" width="560" height="70" fill="var(--navy)"/>
      <rect x="0" y="303" width="560" height="2" fill="#ffffff"/>
    </svg>
    <div class="wordmark">pexla</div>
  </section>
</body>
</html>
```